Uncoded front page web design for wedding and event planning company

Hi.

I am launching a wedding and event planning company called Silver Fern Celebrations and need a professional and appealing web design.

So, let me explain my company. I am based in Swindon in Wiltshire but the company will plan weddings and events in Oxfordshire, Wiltshire, Berkshire and London.

We will plan weddings, birthdays, conferences, product launches, fashion shows and conventions but the main focus of the website at this stage should be the weddings with all the other occasions being covered under a single 'events' heading.

My contact details for the website should be:
Maureen Hollis
maureen@silverferncelebrations.co.uk
01793 587203 / 07781 452638

I'd like the website to feel clean, bright and elegant and be set against a white or off-white background. My logo is purple and I'd therefore like some purple incorporated into the design although feel free to use a more muted purple as my one might be a little bright? I'm also considering whether it would look nice paired with a little of the colour gold - maybe as a font colour in places?? I'll leave you to figure that one out as your design eye will be better than mine but for your reference below is my purple colour and my suggested gold one....

My purple colour is Pantone 2592 C but feel free to use others
My suggested gold I'm looking at is Pantone 14-1041 TCX

I would like to incorporate a Circlepage feed in the front page if possible, if it looks right. I'd also like to include a variety of pictures as well so I've included a few in a Dropbox folder which is linked below. Please don't feel obliged to use them all by any means (there's loads!) but you've got a few there to play with. If you find any other royalty free images you'd rather use please go ahead but on the understanding I can have them afterwards!

My logo can be retrieved via this Dropbox link...
You'll notice there are 2 styles of placement. Please feel free to use either to fit in with your design...
https://www.filevault.example/sh/kq8pw2mzr4tn7ab/BBBQrt6hNxyvpe5L81GmsWd3Pc?dl=0

The wedding images I have are in this Dropbox folder...
https://www.filevault.example/sh/m9vc2xh6pl1qw8j/BBB4zkrNvLpte6P57YhaJoscb?dl=0

Other than that, it's over to you.... I can't wait to receive your designs :-)

Ooh....finally just to say, as I receive designs in I think I'll notice aspects that I like and don't like and if I feel they'll be useful for other designers, I'll update my brief below. Thanks

BRIEF UPDATE:
Someone asked if I had a tag-line. Could you use "Creating exquisite occasions today for amazing memories tomorrow"

I realise I hadn't explained what I'd like included on my home page so here's some notes to consider....

A welcome to section for me to start narrative about us and our services which has a button that links to our 'about us' page and 'services' page for further information.

A section that nicely illustrates what services we offer whether that be with icons or pictures.

A section with some photos in that would link to our gallery

A section that shows some customer reviews and blog entries that would link to my reviews page and blog to read more.

And finally a contact us section with my details, social media links and site map.

***
I also need to draw attention to where in the UK my services cover. I was therefore thinking perhaps we could use a picture to demonstrate this where it highlights Wiltshire, Oxfordshire, Berkshire and London on a map thereby demonstrating our areas covered. I have found several English county maps when searching on Google but I'm not sure how to highlight the areas I cover (or dull out the areas I don't) so if you have any ideas on this, I'd really like it incorporated. Thanks. (by the way, for those of you not familiar with English counties, the ones I cover are often abbreviated to Wilts, Oxon, Berks, London, so if you find a suitable map with those names on rather than the full names, you'll know what they are!)

I've found an image of the county map which might work well. I was wondering whether we might somehow grey out the counties I don't cover and just keep the ones I do as mentioned above and then crop it into perhaps a shadowed circle? I've attached a screenshot to the brief.

I've decided on the tag-line "Creating exquisite occasions today for amazing memories tomorrow" so if that could be included somewhere that would be great. I also need to draw attention to where in the UK my services cover. I was therefore thinking perhaps we could use a picture to demonstrate this where it highlights Wiltshire, Oxfordshire, Berkshire and London on a map thereby demonstrating our areas covered. I have found several English county maps when searching on Google but I'm not sure how to highlight the areas I cover (or dull out the areas I don't) so if you have any ideas on this, I'd really like it incorporated. Thanks. Added Wednesday, June 24, 2015

Target Market(s)

Predominately women aged 25-55

Industry/Entity Type

Wedding Planner

Number of Pages Required

1 page

Font styles to use
Sans Serif
Script

Requirements
Nice to have
• I'd like to see how the colour theme of purple and perhaps a little gold (maybe as a font colour) look against a white background. I've mentioned the Pantone colours in the brief above.
• I've attached a screenshot of a webpage with gold writing in and fonts that I like. Perhaps it could give you inspiration?
Should not have
• I really don't like the font SCRIPTINA so please done use that.

```html
<!DOCTYPE html>
<html lang="en">
<head>
<meta charset="utf-8">
<title>Silver Fern Celebrations</title>
<link rel="stylesheet" href="https://fonts.googleapis.com/css2?family=Cinzel:wght@400&family=Mulish:ital,wght@0,300;0,400;1,300&display=swap">
<style>
:root{
  --purple:#8e1fa3;
  --gold:#e2a246;
  --gold-line:#ebc890;
  --ink:#1f1f1f;
  --grey:#6c6158;
  --page:#ffffff;
  --band:#f3e9dc;
}
*{box-sizing:border-box;margin:0;padding:0}
html,body{width:980px;height:1200px;overflow:hidden}
body{position:relative;font-family:"Mulish",sans-serif;font-weight:300;color:var(--ink);background:#f7f1f0}
.backdrop{position:absolute;inset:0;background:
  radial-gradient(ellipse 260px 200px at 60px 560px,rgba(214,170,90,.45),transparent 70%),
  radial-gradient(ellipse 360px 300px at 80px 1000px,rgba(240,170,190,.55),transparent 70%),
  radial-gradient(ellipse 340px 300px at 920px 1000px,rgba(245,185,190,.55),transparent 70%),
  radial-gradient(ellipse 300px 240px at 880px 160px,rgba(225,230,205,.55),transparent 70%),
  linear-gradient(#f8f5f3,#f6ecec)}
.abs{position:absolute}
.shape{position:absolute;left:0;top:0}
.ghost-word{position:absolute;top:30px;font-family:"Cinzel",serif;font-size:32px;color:#f6e4dc;letter-spacing:1px}
.brand{position:absolute;left:382px;top:28px;width:216px;text-align:center;font-family:"Cinzel",serif;font-size:17px;color:var(--purple);line-height:1.15}
.brand-dot{display:block;width:26px;height:26px;border-radius:50%;background:var(--purple);margin:0 auto 8px}
.nav{position:absolute;left:149px;width:682px;height:16px;display:flex;justify-content:space-between;align-items:center;padding:0 14px;font-family:"Cinzel",serif;font-size:12px;list-style:none}
.nav li{display:flex;align-items:center}
.nav .sep{width:6px;height:6px;border:1px solid currentColor;border-radius:50%;opacity:.7}
.nav-top{top:125px;color:var(--purple);border-top:1px solid #8a8a8a;border-bottom:1px solid #8a8a8a;background:#fff}
.nav-bottom{top:1177px;color:var(--grey)}
.content{position:absolute;left:149px;top:141px;width:682px;height:857px;background:var(--page);border-left:1px solid var(--gold-line);border-right:1px solid var(--gold-line)}
.intro{position:absolute;left:240px;top:24px;width:500px;margin-left:-140px;width:500px;text-align:center;color:var(--gold);font-size:11.4px;line-height:13.4px;left:91px}
.intro p+p{margin-top:13px}
.intro .lead{font-weight:400}
.intro a{color:var(--gold);font-weight:400}
.card{position:absolute;top:169px;width:333px;height:316px;border:1px solid var(--gold-line);border-top:none;border-radius:0 0 14px 14px;background:#fff;overflow:hidden}
.card-photo{height:168px}
.photo-weddings{background:linear-gradient(180deg,#c9bdb3 0%,#e7ddd6 55%,#fff 100%)}
.photo-events{background:linear-gradient(180deg,#b9aea6 0%,#e6d9dc 55%,#fff 100%)}
.card-title{position:absolute;top:18px;left:0;right:0;text-align:center;font-family:"Cinzel",serif;font-size:31px;color:#2b2b2b}
.quote{position:absolute;top:64px;left:40px;right:40px;text-align:center;font-style:italic;font-size:12.3px;line-height:15px;color:#222}
.quote cite{display:block;font-size:10px;margin-top:2px}
.qmark{position:absolute;top:54px;font-family:"Cinzel",serif;font-size:22px;color:#444}
.card-body{position:absolute;top:160px;left:17px;right:17px;font-size:11.4px;line-height:13.4px}
.card-body p+p{margin-top:13px}
.card-body a{color:var(--ink)}
.gallery-title{position:absolute;top:556px;left:0;right:0;text-align:center;font-family:"Cinzel",serif;font-size:30px;color:var(--gold)}
.thumb{position:absolute;width:100px;height:100px;border:1px solid var(--gold-line);padding:6px;background:#fff}
.thumb span{display:block;width:100%;height:100%;border:1px dashed #f0d9b6}
.arrow{position:absolute;top:0}
.quote-btn{position:absolute;left:403px;top:1022px;width:174px;height:72px;border:1px solid var(--purple);border-radius:50%;display:flex;align-items:center;justify-content:center;text-align:center;font-family:"Cinzel",serif;font-size:15px;line-height:18px;color:var(--gold);background:rgba(255,255,255,.85)}
.social{position:absolute;font-size:11.4px;color:var(--gold)}
.social .txt{position:absolute;right:0;white-space:nowrap}
.dot-icon{position:absolute;width:13px;height:13px;border:1.3px solid var(--gold);border-radius:50%}
.contact{position:absolute;font-size:11.4px;color:var(--gold);white-space:nowrap}
</style>
</head>
<body>
<div class="backdrop" role="img" aria-label="Soft blurred photograph of gold wedding rings and pale pink roses"></div>

<svg class="shape" width="980" height="1200" aria-hidden="true">
  <path d="M131,0 H849 V84 Q760 104 612 102 Q598 104 598 118 V125 H382 V118 Q382 104 368 102 Q220 104 131 84 Z" fill="#fff"/>
  <path d="M131,84 Q220 104 368 102 M612 102 Q760 104 849 84" stroke="var(--gold-line)" fill="none"/>
  <path d="M384 100 C384 40 430 10 490 10 C550 10 596 40 596 100" stroke="#f1dcc0" fill="none"/>
  <path d="M131,1200 V1040 Q220 1022 368 1028 Q382 1028 384 1015 C390 992 590 992 596 1015 Q598 1028 612 1028 Q760 1022 849 1040 V1200 Z" fill="#fff"/>
  <path d="M131,1040 Q220 1022 368 1028 Q382 1028 384 1015 C390 992 590 992 596 1015 Q598 1028 612 1028 Q760 1022 849 1040" stroke="var(--gold-line)" fill="none"/>
  <rect x="131" y="1169" width="718" height="31" fill="var(--band)"/>
  <line x1="131" y1="1169" x2="849" y2="1169" stroke="#d9c6ad"/>
</svg>

<div class="ghost-word" style="left:176px">WEDDINGS</div>
<div class="ghost-word" style="left:657px">EVENTS</div>
<div class="brand"><span class="brand-dot"></span>Silver Fern Celebrations</div>

<ul class="nav nav-top">
  <li>Weddings</li><li class="sep"></li><li>Birthdays</li><li class="sep"></li><li>Conferences</li><li class="sep"></li><li>Product Launches</li><li class="sep"></li><li>Fashion Shows</li><li class="sep"></li><li>Conventions</li>
</ul>

<main class="content">
  <section class="intro">
    <p><span class="lead">Silver Fern Celebrations plan weddings and events in Oxfordshire, Wiltshire, Berkshire and London.</span><br>Lorem ipsum dolor sit amet, consectetuer adipiscing elit. Suspendisse hendrerit ligula quis velit pharetra egestas. Ut molestie elit non massa. Vivamus tincidunt bibendum velit. Quisque nisl diam, nonummy eu, lobortis consequat, mollis ut, tellus. In iaculis. <a href="#">This is a link.</a></p>
    <p>Etiam sagittis nulla at quam. In massa. Integer leo tortor, dignissim nec, volutpat id, luctus non, nisi. Morbi iaculis mollis felis. Ut ullamcorper tortor. <a href="#">Read More.</a></p>
  </section>

  <article class="card" style="left:0">
    <div class="card-photo photo-weddings" role="img" aria-label="Faded photo of a bride and groom holding hands"></div>
    <h2 class="card-title">WEDDINGS</h2>
    <span class="qmark" style="left:40px">“</span><span class="qmark" style="right:36px">”</span>
    <blockquote class="quote">Wonderful wedding planner, made it effortless, extremely attractive and a resounding success!<cite>— Clara Bellamy</cite></blockquote>
    <div class="card-body">
      <p>Etiam varius sapien in turpis. Suspendisse eros nibh, cursus vel, malesuada id, ullamcorper et, odio. Proin ac velit et ligula aliquam molestie. Proin congue sapien eget nunc. Sed at orci. Aenean ornare, velit eget bibendum adipiscing, turpis ante cursus mauris, in porta dolor mauris eget mi.</p>
      <p>Nulla tincidunt semper lorem. Nunc vitae urna eget mi convallis iaculis. Ut tincidunt ullamcorper lectus. Integer interdum, nisi ac sollicitudin rhoncus, quam nisl mollis enim, eget condimentum erat purus eu orci.</p>
    </div>
  </article>

  <article class="card" style="left:348px">
    <div class="card-photo photo-events" role="img" aria-label="Faded photo of guests dining at an event table"></div>
    <h2 class="card-title">EVENTS</h2>
    <span class="qmark" style="left:40px">“</span><span class="qmark" style="right:36px">”</span>
    <blockquote class="quote">Excellent event planner, very creative, pays attention to all the details and would not hesitate to use again!<cite>— Tom R. Ashby</cite></blockquote>
    <div class="card-body">
      <p>Etiam varius sapien in turpis. Suspendisse eros nibh, cursus vel, malesuada id, ullamcorper et, odio. Proin ac velit et ligula aliquam molestie. Proin congue sapien eget nunc. Sed at orci. Aenean ornare, velit eget bibendum adipiscing, turpis ante cursus mauris, in porta dolor mauris eget mi. <a href="#">This is another link.</a></p>
      <p>Nulla tincidunt semper lorem. Nunc vitae urna eget mi convallis iaculis. Ut tincidunt ullamcorper lectus. Integer interdum, nisi ac sollicitudin rhoncus, quam nisl mollis enim, eget condimentum erat purus eu orci.</p>
    </div>
  </article>

  <svg class="shape" width="682" height="857" aria-hidden="true" style="left:-1px">
    <path d="M0 555 Q10 555 14 543 H668 Q672 555 682 555" stroke="var(--gold-line)" fill="none"/>
    <path d="M0 843 Q10 843 14 857 M668 857 Q672 843 682 843" stroke="var(--gold-line)" fill="none"/>
  </svg>
  <h2 class="gallery-title">GALLERY</h2>
</main>

<div class="thumb" style="left:208px;top:751px"><span role="img" aria-label="Pink and white rose bouquet" style="background:linear-gradient(135deg,#e9b7c8,#c7587f)"></span></div>
<div class="thumb" style="left:324px;top:751px"><span role="img" aria-label="Bride in a lace dress holding flowers" style="background:linear-gradient(135deg,#efe6df,#b89a86)"></span></div>
<div class="thumb" style="left:441px;top:751px"><span role="img" aria-label="Couple by a stone wall with white flowers" style="background:linear-gradient(135deg,#d6d2cc,#8c8a86)"></span></div>
<div class="thumb" style="left:557px;top:751px"><span role="img" aria-label="Couple signing the wedding register" style="background:linear-gradient(135deg,#4a4f6b,#e8e6ea)"></span></div>
<div class="thumb" style="left:673px;top:751px"><span role="img" aria-label="Pale rose posy" style="background:linear-gradient(135deg,#f5eeea,#e6b9b9)"></span></div>
<div class="thumb" style="left:208px;top:868px"><span role="img" aria-label="Bridal bouquet on a wooden table" style="background:linear-gradient(135deg,#e7d9cf,#7a5a48)"></span></div>
<div class="thumb" style="left:324px;top:868px"><span role="img" aria-label="Champagne in a silver bucket" style="background:linear-gradient(135deg,#f4efe6,#b8965a)"></span></div>
<div class="thumb" style="left:441px;top:868px"><span role="img" aria-label="Reception hall set with white tables" style="background:linear-gradient(135deg,#c9b990,#f0ece4)"></span></div>
<div class="thumb" style="left:557px;top:868px"><span role="img" aria-label="Lacing the back of a wedding dress" style="background:linear-gradient(135deg,#e9e3de,#b7aca5)"></span></div>
<div class="thumb" style="left:673px;top:868px"><span role="img" aria-label="Bride having her hair styled" style="background:linear-gradient(135deg,#a86c58,#e6d0c4)"></span></div>

<svg class="arrow" style="left:172px;top:846px" width="16" height="20" aria-hidden="true"><path d="M13 2 L3 10 L13 18" stroke="var(--gold)" stroke-width="3" fill="none"/></svg>
<svg class="arrow" style="left:793px;top:846px" width="16" height="20" aria-hidden="true"><path d="M3 2 L13 10 L3 18" stroke="var(--gold)" stroke-width="3" fill="none"/></svg>

<a class="quote-btn">CLICK FOR AN<br>ONLINE QUOTE</a>

<div class="social" style="left:150px;top:1084px;width:195px"><span class="txt">Follow us on Circlepage</span></div>
<span class="dot-icon" style="left:355px;top:1084px"></span>
<div class="social" style="left:150px;top:1110px;width:212px"><span class="txt">Read our tweets and posts on Chirper</span></div>
<span class="dot-icon" style="left:376px;top:1110px"></span>
<div class="social" style="left:150px;top:1133px;width:252px"><span class="txt">Connect with us on Workline</span></div>
<span class="dot-icon" style="left:414px;top:1133px"></span>

<svg class="abs" style="left:605px;top:1081px" width="16" height="19" aria-hidden="true"><circle cx="8" cy="5.5" r="4.3" stroke="var(--gold)" stroke-width="1.3" fill="none"/><path d="M1 18 V15 Q1 10.5 8 10.5 Q15 10.5 15 15 V18 Z" stroke="var(--gold)" stroke-width="1.3" fill="none"/></svg>
<div class="contact" style="left:627px;top:1084px">Maureen Hollis</div>
<svg class="abs" style="left:578px;top:1108px" width="20" height="20" aria-hidden="true"><path d="M4 2 L8 6 L6 9 Q9 13 12 15 L15 13 L18 17 L15 19 Q4 15 1 5 Z" stroke="var(--gold)" stroke-width="1.3" fill="none" stroke-linejoin="round"/></svg>
<div class="contact" style="left:607px;top:1111px">01793 587203 / 07781 452638</div>
<svg class="abs" style="left:548px;top:1134px" width="20" height="14" aria-hidden="true"><rect x="1" y="1" width="18" height="12" stroke="var(--gold)" stroke-width="1.3" fill="none"/><path d="M1 1 L10 8 L19 1" stroke="var(--gold)" stroke-width="1.3" fill="none"/></svg>
<div class="contact" style="left:578px;top:1133px">maureen@silverferncelebrations.co.uk</div>

<ul class="nav nav-bottom">
  <li>Weddings</li><li class="sep"></li><li>Birthdays</li><li class="sep"></li><li>Conferences</li><li class="sep"></li><li>Product Launches</li><li class="sep"></li><li>Fashion Shows</li><li class="sep"></li><li>Conventions</li>
</ul>
</body>
</html>
```